Veldmark Supplies Business Card

Professional business card that stand out to our potential customers. Front and back with clean modern design

Industry/Entity Type

Oil and gas

Contact Information for Business Card

Name, address, website , office phone and cell number

Requirements
Must have
• Editable files for each employee

```html
<!DOCTYPE html>
<html lang="en">
<head>
<meta charset="utf-8">
<title>Veldmark Supplies Business Card</title>
<link href="https://fonts.googleapis.com/css2?family=Arimo:wght@400;700&display=swap" rel="stylesheet">
<style>
  :root {
    --stage: #3d3d3d;
    --brand-blue: #05afd0;
    --brand-red: #ff0000;
    --white: #ffffff;
    --card-w: 540px;
    --card-h: 309px;
  }
  * { margin: 0; padding: 0; box-sizing: border-box; }
  html, body {
    width: 1200px; height: 803px; overflow: hidden;
    background: var(--stage);
    font-family: "Arimo", Arial, sans-serif;
  }
  .stage {
    position: relative; width: 1200px; height: 803px;
    display: flex; align-items: center; justify-content: center; gap: 40px;
  }
  .card {
    position: relative; width: var(--card-w); height: var(--card-h);
    border-radius: 22px; overflow: hidden;
  }
  .card-front { background: var(--brand-blue); }
  .card-back { background: var(--brand-red); }

  .front-corner { position: absolute; inset: 0; }

  .front-mark {
    position: absolute; right: 34px; top: 74px;
    display: flex; align-items: center; gap: 10px;
    color: var(--brand-red); font-weight: 700; font-size: 30px;
    line-height: 1.05; text-transform: uppercase; text-align: left;
  }
  .mark-square { width: 22px; height: 22px; background: var(--brand-red); flex: none; }

  .front-details {
    position: absolute; left: 34px; bottom: 28px; color: var(--white);
  }
  .company-line {
    font-weight: 700; font-size: 15px; letter-spacing: 1px;
    text-transform: uppercase; margin-bottom: 14px;
  }
  .person-name { font-weight: 700; font-size: 24px; text-transform: uppercase; line-height: 1; }
  .person-title { font-size: 13px; margin-top: 3px; margin-bottom: 12px; }
  .address { font-size: 13px; line-height: 1.3; margin-bottom: 10px; }
  .contact-list { list-style: none; font-size: 13px; line-height: 1.35; }
  .contact-list li { display: flex; align-items: center; gap: 8px; }
  .contact-list svg { width: 12px; height: 12px; flex: none; }

  .back-mark {
    position: absolute; inset: 0;
    display: flex; align-items: center; justify-content: center; gap: 12px;
    color: var(--white); font-weight: 700; font-size: 34px; text-transform: uppercase;
  }
  .back-mark .mark-square { background: var(--white); width: 26px; height: 26px; }
</style>
</head>
<body>
<main class="stage">

  <section class="card card-front" aria-label="Card front">
    <svg class="front-corner" viewBox="0 0 540 309" preserveAspectRatio="none" aria-hidden="true">
      <polygon points="250,0 540,0 540,120 430,309 540,309 540,0" fill="#ffffff"/>
      <polygon points="250,0 540,0 540,150 420,309 540,309" fill="#ffffff"/>
    </svg>
    <div class="front-mark">
      <span class="mark-square"></span>
      <span>Veldmark<br>Supplies</span>
    </div>

    <div class="front-details">
      <p class="company-line">Veldmark Supplies</p>
      <p class="person-name">Aaron Pike</p>
      <p class="person-title">President</p>
      <p class="address">4120 Ridgeway Drive<br>Calgary, Canada 55210</p>
      <ul class="contact-list">
        <li>
          <svg viewBox="0 0 12 12" aria-hidden="true"><path d="M2 1h3l1 3-2 1a6 6 0 0 0 3 3l1-2 3 1v3c-6 0-10-4-10-10z" fill="#ff0000"/></svg>
          555-210-4871
        </li>
        <li>
          <svg viewBox="0 0 12 12" aria-hidden="true"><rect x="3" y="0.5" width="6" height="11" rx="1" fill="none" stroke="#ff0000" stroke-width="1.4"/></svg>
          555-210-9326
        </li>
        <li>
          <svg viewBox="0 0 12 12" aria-hidden="true"><rect x="0.5" y="2" width="11" height="8" fill="#ff0000"/><path d="M1 2.5l5 4 5-4" fill="none" stroke="#05afd0" stroke-width="1"/></svg>
          info@veldmarksupplies.com
        </li>
        <li>
          <svg viewBox="0 0 12 12" aria-hidden="true"><circle cx="6" cy="6" r="5.3" fill="#ff0000"/><path d="M0.7 6h10.6M6 0.7c-2.5 3-2.5 7.6 0 10.6M6 0.7c2.5 3 2.5 7.6 0 10.6" fill="none" stroke="#05afd0" stroke-width="0.8"/></svg>
          www.veldmarksupplies.com
        </li>
      </ul>
    </div>
  </section>

  <section class="card card-back" aria-label="Card back">
    <div class="back-mark">
      <span class="mark-square"></span>
      <span>Veldmark Supplies</span>
    </div>
  </section>

</main>
</body>
</html>
```